New Innovative Counselling and psychotherapy Service needs Business Card design

Keep it simple and professional. On one side, just company name and logo (perhaps in all blue) and maybe a tag line.

On other side (all white) my name and Qualifications in centre

Industry/Entity Type

Health And Wellness

Contact Information for Business Card

Dara Whelby
Counsellor & Psychotherapist
BSc (Psychol.), BA, Dip. (Couns. & Psych.), PG.Cert (CBT), FGTrK, ONRE

I will also require Mobile no, Email and web site address of which I'll pass on to final designer.

Font styles to use
Sans Serif

Requirements
Must have
• My Logo Only and please use the colours in logo that is in it.
Should not have
• Any other images

```html
<!DOCTYPE html>
<html lang="en">
<head>
<meta charset="utf-8">
<title>Brightway Grove – Business Card</title>
<link rel="stylesheet" href="https://fonts.googleapis.com/css2?family=Lato:wght@400&family=Roboto+Condensed:wght@400&display=swap">
<style>
  :root {
    --canvas: #e9eaec;
    --card: #ffffff;
    --ink: #333333;
    --blue: #3fb0ea;
    --green: #8cc63f;
  }
  * { margin: 0; padding: 0; box-sizing: border-box; }
  html, body { width: 1200px; height: 900px; overflow: hidden; background: var(--canvas); }
  body { position: relative; font-family: "Lato", Arial, sans-serif; color: var(--ink); }

  .card {
    position: absolute; left: 160px; top: 176px;
    width: 880px; height: 548px;
    background: var(--card);
    border-radius: 274px 0 0 274px;
    box-shadow: 0 6px 24px rgba(0,0,0,0.12);
    overflow: hidden;
  }
  .accent-bar { position: absolute; right: 0; width: 16px; }
  .accent-bar--blue { top: 68px; height: 122px; background: var(--blue); }
  .accent-bar--green { top: 413px; height: 88px; background: var(--green); }

  .identity { position: absolute; right: 37px; top: 60px; text-align: right; }
  .identity__name { font-size: 31px; letter-spacing: 0.5px; line-height: 40px; text-transform: uppercase; font-weight: 400; }
  .identity__first { color: var(--blue); }
  .identity__last { color: var(--green); }
  .identity__role, .identity__quals { font-size: 22px; line-height: 32px; }

  .brand { position: absolute; left: 54px; top: 222px; display: flex; align-items: center; gap: 30px; }
  .brand__dot { width: 100px; height: 100px; border-radius: 50%; background: var(--blue); flex: none; }
  .brand__name { font-size: 50px; color: var(--ink); font-weight: 400; letter-spacing: 0.3px; }

  .tagline { position: absolute; left: 78px; top: 350px; font-family: "Roboto Condensed", "Arial Narrow", sans-serif; font-size: 24px; color: var(--ink); }

  .contact { position: absolute; right: 37px; top: 410px; list-style: none; text-align: right; }
  .contact__item { font-size: 22px; line-height: 32.5px; display: flex; justify-content: flex-end; align-items: center; gap: 8px; }
  .contact__icon { width: 20px; height: 20px; flex: none; }
</style>
</head>
<body>
  <section class="card" aria-label="Business card">
    <div class="accent-bar accent-bar--blue"></div>
    <div class="accent-bar accent-bar--green"></div>

    <div class="identity">
      <h1 class="identity__name"><span class="identity__first">Dara</span> <span class="identity__last">Whelby</span></h1>
      <p class="identity__role">Counsellor &amp; Psychotherapist</p>
      <p class="identity__quals">BSc (Psychol.), BA, Dip. (Couns. &amp; Psych.)</p>
      <p class="identity__quals">PG.Cert (CBT), FGTrK, ONRE</p>
    </div>

    <div class="brand">
      <span class="brand__dot" aria-hidden="true"></span>
      <span class="brand__name">Brightway Grove</span>
    </div>

    <p class="tagline">Caring For Your Psychological Well-Being Is Our Top Priority</p>

    <ul class="contact">
      <li class="contact__item">086 5520 417
        <svg class="contact__icon" viewBox="0 0 20 20" aria-hidden="true">
          <path fill="#3fb0ea" d="M3 8c0-3 3-5 7-5s7 2 7 5l-3 1-1-2H7L6 9zM5 11h10l1 6H4z"/>
        </svg>
      </li>
      <li class="contact__item">info@brightwaygrove.com
        <svg class="contact__icon" viewBox="0 0 20 20" aria-hidden="true">
          <rect x="2" y="5" width="16" height="11" fill="#3fb0ea"/>
          <path d="M2 5l8 6 8-6" fill="none" stroke="#fff" stroke-width="1.5"/>
        </svg>
      </li>
      <li class="contact__item">www.brightwaygrove.com
        <svg class="contact__icon" viewBox="0 0 20 20" aria-hidden="true">
          <circle cx="10" cy="10" r="8" fill="#3fb0ea"/>
          <path d="M6 6c2 0 3 2 2 3s-2 2 0 4M13 5c-1 2 1 3 2 3M12 15c0-2 2-2 3-3" fill="none" stroke="#fff" stroke-width="1.4"/>
        </svg>
      </li>
    </ul>
  </section>
</body>
</html>
```